Create modern and sleek business card for luxury real estate company

We're a "boutique" real estate office looking for a design that gets across a highly modern luxury brand. Blacks and whites are probably the best colors unless we try a silver foil for the logo. I've attached a version of our current logo here. I'd like to swap out the current font on there with Gotham Light Regular.

I'm looking to have one side of the card have the logo with the space for our agents info on the other side.

Target Market(s)

Young professionals in a "luxury" headspace

Industry/Entity Type

Real estate

Contact Information for Business Card

A place for agent name, cell number, website. The slogan "Simply Rethinking Real Estate".

Font styles to use
Other font styles liked:
• Gotham Regular

Colors

Designer to choose only greyscale colors for use in the design.

Requirements
Must have
• Matte black as the background color. Clean lines and use of contrast. A specific design aspect that will use silver foil.
Nice to have
• Up in the air on integrating a QR code
Should not have
• Any houses or other real estate related design (ex: a clip art house)

```html
<!DOCTYPE html>
<html lang="en">
<head>
<meta charset="utf-8">
<title>Halden Estates – Business Card</title>
<link rel="stylesheet" href="https://fonts.googleapis.com/css2?family=Tinos:wght@400;700&family=Arimo:wght@400&display=swap">
<style>
  :root {
    --page-bg: #141414;
    --card-edge: #0d0d0d;
    --panel-dark: #161616;
    --panel-light: #3a3a3a;
    --ink: #f2f2f2;
    --ink-soft: #d8d8d8;
    --frame-line: #e6e6e6;
    --divider: rgba(255,255,255,0.14);
  }
  * { margin: 0; padding: 0; box-sizing: border-box; }
  html, body { width: 1200px; height: 1015px; overflow: hidden; }
  body {
    background: var(--page-bg);
    position: relative;
    font-family: "Arimo", Arial, sans-serif;
    color: var(--ink);
  }
  .card {
    position: absolute;
    left: 190px;
    width: 820px;
    height: 460px;
    background: var(--card-edge);
    box-shadow: 0 18px 40px rgba(0,0,0,0.6);
  }
  .card--front { top: 30px; }
  .card--back { top: 525px; }
  .card__panel {
    position: absolute;
    inset: 38px;
    border: 2px solid var(--frame-line);
    background: radial-gradient(ellipse at 50% 45%, var(--panel-light) 0%, var(--panel-dark) 75%);
  }
  .brand {
    position: absolute;
    display: flex;
    align-items: center;
    gap: 22px;
  }
  .brand__circle {
    flex: none;
    border: 3px solid var(--ink);
    border-radius: 50%;
  }
  .brand__name {
    font-family: "Tinos", "Times New Roman", serif;
    font-weight: 400;
    color: var(--ink);
    letter-spacing: 0.06em;
    line-height: 1.05;
    text-transform: uppercase;
  }
  .card--front .brand { left: 50%; top: 50%; transform: translate(-50%, -50%); }
  .card--front .brand__circle { width: 110px; height: 110px; }
  .card--front .brand__name { font-size: 52px; }
  .card--back .brand { left: 70px; top: 50%; transform: translateY(-50%); }
  .card--back .brand__circle { width: 78px; height: 78px; border-width: 2px; }
  .card--back .brand__name { font-size: 36px; }
  .card__divider {
    position: absolute;
    left: 52%;
    top: 36px;
    bottom: 36px;
    width: 1px;
    background: var(--divider);
  }
  .agent {
    position: absolute;
    left: 56%;
    top: 58px;
  }
  .agent__name {
    font-family: "Tinos", "Times New Roman", serif;
    font-weight: 700;
    font-size: 27px;
    letter-spacing: 0.04em;
    text-transform: uppercase;
  }
  .agent__role {
    font-size: 18px;
    color: var(--ink-soft);
    margin-top: 2px;
  }
  .agent__contacts {
    list-style: none;
    margin-top: 22px;
    font-size: 19px;
    line-height: 1.45;
  }
  .agent__contacts li { display: flex; align-items: center; gap: 8px; }
  .agent__contacts svg { width: 17px; height: 17px; flex: none; }
  .agent__address {
    font-style: normal;
    font-size: 19px;
    line-height: 1.4;
    margin-top: 18px;
    padding-left: 25px;
  }
</style>
</head>
<body>

<section class="card card--front" aria-label="Card front">
  <div class="card__panel">
    <div class="brand">
      <span class="brand__circle" aria-hidden="true"></span>
      <span class="brand__name">Halden<br>Estates</span>
    </div>
  </div>
</section>

<section class="card card--back" aria-label="Card back">
  <div class="card__panel">
    <div class="brand">
      <span class="brand__circle" aria-hidden="true"></span>
      <span class="brand__name">Halden<br>Estates</span>
    </div>
    <div class="card__divider"></div>
    <div class="agent">
      <div class="agent__name">Marcus Hale</div>
      <div class="agent__role">Managing Director</div>
      <ul class="agent__contacts">
        <li>
          <svg viewBox="0 0 24 24" fill="none" stroke="#f2f2f2" stroke-width="2" stroke-linecap="round" stroke-linejoin="round"><path d="M5 3h4l2 5-2.5 1.5a11 11 0 0 0 6 6L16 13l5 2v4a2 2 0 0 1-2 2A16 16 0 0 1 3 5a2 2 0 0 1 2-2z"/></svg>
          071-868 302 915
        </li>
        <li>
          <svg viewBox="0 0 24 24" fill="#f2f2f2"><path d="M2 5h20v14H2z"/><path d="M2 5l10 8 10-8" fill="none" stroke="#222" stroke-width="1.6"/></svg>
          hello@haldenestates.com
        </li>
        <li>
          <svg viewBox="0 0 24 24" fill="none" stroke="#f2f2f2" stroke-width="1.8"><circle cx="12" cy="12" r="9"/><path d="M3 12h18M12 3c3 3 3 15 0 18M12 3c-3 3-3 15 0 18"/></svg>
          www.haldenestates.com
        </li>
      </ul>
      <address class="agent__address">18, Marlow Crescent<br>30918, Northbridge</address>
    </div>
  </div>
</section>

</body>
</html>
```